Landingpage Design X-Mas Invitation

Every year we invite customers to a special X-Mas Apéro. Since we are an IT-Company we handle the registration process by a landingpage. For this we need a design for the event 2016. The content will be the same as 2015 (you will finde the design attached from last year. There will be an additional job for creating the E-Mail.

Target Market(s)

Customers of IT Company, medium Companys in Central Switzerland

Industry/Entity Type

It Company

Number of Pages Required

1 page

Requirements
Must have
• Christmas Style

```html
<!DOCTYPE html>
<html lang="de">
<head>
<meta charset="utf-8">
<title>Lumina Weihnachtsapéro</title>
<link rel="stylesheet" href="https://fonts.googleapis.com/css2?family=Open+Sans:wght@400;700&family=Roboto+Condensed:wght@400&family=Roboto:wght@400&display=swap">
<style>
:root{
  --red-core:#b30a0a;
  --red-deep:#5e0202;
  --snow:#f4eded;
  --snow-shade:#e8d2d2;
  --white:#ffffff;
  --brand-red:#c23a2a;
  --footer:#2d2d2d;
  --footer-line:#444444;
  --partner:#9a9a9a;
  --tree:#3f6a1c;
}
*{margin:0;padding:0;box-sizing:border-box}
html,body{width:1200px;height:955px;overflow:hidden}
body{position:relative;font-family:"Roboto Condensed",sans-serif;color:var(--white);background:var(--footer)}
.hero{position:absolute;left:0;top:0;width:1200px;height:793px;overflow:hidden;
  background:radial-gradient(ellipse 75% 80% at 45% 55%,var(--red-core) 0%,#8c0404 55%,var(--red-deep) 100%)}
.snow{position:absolute;left:0;top:530px;width:1200px;height:263px}
.tree-art{position:absolute;left:68px;top:86px;width:520px;height:540px;
  background:radial-gradient(ellipse 50% 55% at 50% 55%,var(--tree) 0%,rgba(63,106,28,.6) 55%,rgba(63,106,28,0) 80%)}
.tree-label{position:absolute;font-size:16px;line-height:17px;text-align:center;transform-origin:center;white-space:nowrap}
.label-name{left:176px;top:130px;transform:rotate(-55deg)}
.label-date{left:410px;top:248px;transform:rotate(-55deg)}
.label-place{left:58px;top:352px;transform:rotate(-48deg)}
.tree-brand{position:absolute;left:270px;top:644px;color:var(--brand-red);font-family:"Open Sans",sans-serif}
.tree-brand .name{font-size:26px;font-weight:700;line-height:26px;display:block}
.tree-brand .sub{font-size:8px;display:block;text-align:right;color:#555;letter-spacing:.5px}
.brand{position:absolute;left:582px;top:98px;font-family:"Open Sans",sans-serif}
.brand .name{font-size:46px;font-weight:700;line-height:46px;display:block;letter-spacing:-.5px}
.brand .sub{font-size:13px;letter-spacing:1.5px;display:block;text-align:right;margin-top:-2px}
.intro{position:absolute;left:582px;top:186px;width:525px;font-size:13.4px;line-height:22.3px}
.intro p+p{margin-top:15px}
.cta{position:absolute;left:582px;top:444px;font-family:"Roboto",sans-serif;font-size:25px;color:var(--white);text-decoration:none;letter-spacing:.5px}
.partners{position:absolute;left:76px;top:728px;width:1024px;height:40px;display:flex;justify-content:space-between;align-items:center}
.partner{display:block;height:24px;background:var(--partner);border-radius:3px;opacity:.75}
.footer-main{position:absolute;left:0;top:793px;width:1200px;height:100px}
.footer-brand{position:absolute;left:97px;top:26px;font-family:"Open Sans",sans-serif}
.footer-brand .name{font-size:38px;font-weight:700;line-height:38px;display:block}
.footer-brand .sub{font-size:12px;letter-spacing:1px;display:block;text-align:right}
.contact{position:absolute;top:30px;display:flex;gap:14px;font-family:"Open Sans",sans-serif;font-size:13.5px;line-height:20px}
.contact svg{flex:none}
.contact-address{left:353px;width:320px}
.contact-phone{left:713px;font-size:15px}
.contact-phone strong{font-weight:700}
.contact-mail{left:923px}
.footer-rule{position:absolute;left:0;top:893px;width:1200px;height:1px;background:var(--footer-line)}
.copyright{position:absolute;left:0;top:918px;width:1200px;text-align:center;font-family:"Roboto Condensed",sans-serif;font-size:13.5px}
</style>
</head>
<body>
<section class="hero">
  <svg class="snow" viewBox="0 0 1200 263" preserveAspectRatio="none" aria-hidden="true">
    <path d="M0 60 C200 20 420 90 620 40 C820 -5 1000 50 1200 30 L1200 263 L0 263Z" fill="#d9a9a9" opacity=".45"/>
    <path d="M0 80 C250 140 480 30 700 70 C900 105 1050 60 1200 70 L1200 263 L0 263Z" fill="var(--snow-shade)" opacity=".8"/>
    <path d="M0 140 C220 100 460 170 720 130 C940 100 1080 150 1200 110 L1200 263 L0 263Z" fill="#f0e2e2"/>
    <path d="M0 170 C300 200 600 150 900 175 C1050 188 1140 170 1200 165 L1200 263 L0 263Z" fill="var(--snow)"/>
  </svg>
  <div class="tree-art" role="img" aria-label="Illustration eines geschmückten Weihnachtsbaums mit Stern, Kerzen, Kugeln, Girlanden und Geschenken"></div>
  <div class="tree-label label-name">Lumina<br>Weihnachts<br>apéro</div>
  <div class="tree-label label-date">17. Dezember 2015<br>17 - 20 Uhr</div>
  <div class="tree-label label-place">Skylounge<br>Tannenweg 12<br>Luzern</div>
  <div class="tree-brand"><span class="name">Lumina</span><span class="sub">IT SOLUTIONS</span></div>

  <div class="brand"><span class="name">Lumina</span><span class="sub">IT SOLUTIONS</span></div>
  <div class="intro">
    <p>Unser traditioneller Lumina Weihnachtsapéro findet am Donnerstag, dem 17.12.2015, zwischen 17 und 20 Uhr in unserer Skylounge am Tannenweg 12, dem Hauptsitz der Lumina IT Solutions AG statt. In einem aussergewöhnlichen Ambiente können Sie und Ihre Begleitung köstliche Speisen und Getränke beim Apéro Riche geniessen. Desweiteren bietet sich Ihnen die Gelegenheit, ausgiebige Gespräche mit unserer Geschäftsleitung, unseren Mitarbeitenden sowie weiteren Kunden zu führen. Der Anlass findet in einer lockeren Atmosphäre statt, entsprechend ungezwungen ist der Dresscode.</p>
    <p>Ob Sie den ganzen Abend bleiben oder nur kurz nach dem Weihnachts-Shopping vorbeis­chauen, ist ganz Ihnen überlassen. Wir freuen uns sehr, wenn Sie uns die Gelegenheit geben, Ihnen mit dieser Einladung für die erfolgreiche Zusammenarbeit herzlichst zu danken.</p>
  </div>
  <a class="cta" href="#anmelden">ANMELDEN</a>

  <div class="partners" aria-label="Partner">
    <span class="partner" style="width:38px;height:38px;border-radius:50%"></span>
    <span class="partner" style="width:122px"></span>
    <span class="partner" style="width:62px"></span>
    <span class="partner" style="width:46px"></span>
    <span class="partner" style="width:120px"></span>
    <span class="partner" style="width:80px"></span>
    <span class="partner" style="width:66px"></span>
    <span class="partner" style="width:88px;height:30px"></span>
    <span class="partner" style="width:62px"></span>
    <span class="partner" style="width:78px"></span>
    <span class="partner" style="width:108px"></span>
  </div>
</section>

<footer>
  <div class="footer-main">
    <div class="footer-brand"><span class="name">Lumina</span><span class="sub">IT SOLUTIONS</span></div>
    <div class="contact contact-address">
      <svg width="40" height="40" viewBox="0 0 40 40" aria-hidden="true"><circle cx="20" cy="20" r="18.5" fill="none" stroke="#fff" stroke-width="1.2"/><path d="M20 11a6 6 0 0 0-6 6c0 4.5 6 11 6 11s6-6.5 6-11a6 6 0 0 0-6-6z" fill="none" stroke="#fff" stroke-width="1.6"/><circle cx="20" cy="17" r="2" fill="#fff"/></svg>
      <div>KONTAKT :&nbsp;&nbsp; Lumina IT Solutions AG Tannen­weg 12 6004 Luzern</div>
    </div>
    <div class="contact contact-phone">
      <svg width="40" height="40" viewBox="0 0 40 40" aria-hidden="true"><circle cx="20" cy="20" r="18.5" fill="none" stroke="#fff" stroke-width="1.2"/><path d="M14 12c1-1 2-1 3 0l2 3c.5 1 0 2-1 2.5-.5.3-.5 1 0 2l2.5 2.5c1 .5 1.7.5 2 0 .5-1 1.5-1.5 2.5-1l3 2c1 1 1 2 0 3-2 2-5 2-9-2s-6-9-5-12z" fill="#fff"/></svg>
      <div>Telefon:<br><strong>041 555 01 20</strong></div>
    </div>
    <div class="contact contact-mail">
      <svg width="40" height="40" viewBox="0 0 40 40" aria-hidden="true"><circle cx="20" cy="20" r="18.5" fill="none" stroke="#fff" stroke-width="1.2"/><path d="M20 11a6 6 0 0 0-6 6c0 4.5 6 11 6 11s6-6.5 6-11a6 6 0 0 0-6-6z" fill="none" stroke="#fff" stroke-width="1.6"/><circle cx="20" cy="17" r="2" fill="#fff"/></svg>
      <div>Email:<br>info@lumina-it.example</div>
    </div>
  </div>
  <div class="footer-rule"></div>
  <p class="copyright">© Copyright 2016 Lumina . All Rights Reserved.</p>
</footer>
</body>
</html>
```